MEDICAL CLINIC LETTERHEAD

Design is a letterhead for a non-profit medical center. The name of the clinic is VITARIDGE Community Health Center. Although the full name must be included, the community health center part is more of a description and should be less visible - i attached an example of what I mean by that (ATTACHED IMAGE IS AN EXAMPLE OF FONT SIZES NOT A DESIGN IDEA). Please design something modern, cool looking and unique because I can always download free templates.
Phone, email, website and etc will be added later.

Industry/Entity Type

MEDICAL

```html
<!DOCTYPE html>
<html lang="en">
<head>
<meta charset="utf-8">
<title>VITARIDGE Community Health Center — Letterhead</title>
<link href="https://fonts.googleapis.com/css2?family=Montserrat:wght@500;700&family=Questrial&family=Open+Sans:wght@600&display=swap" rel="stylesheet">
<style>
  :root {
    --paper: #ffffff;
    --ink-dark: #4a4a4c;
    --ink-grey: #8e8e90;
    --ink-body: #9a9a9c;
    --brand-green: #1a9b47;
    --footer-text: #ffffff;
    --ghost: #f0f1f2;
    --signature-fill: #ececec;
  }
  * { margin: 0; padding: 0; box-sizing: border-box; }
  html, body { width: 908px; height: 1200px; overflow: hidden; background: var(--paper); }
  .letterhead {
    position: relative;
    width: 908px;
    height: 1200px;
    background: var(--paper);
    font-family: "Questrial", sans-serif;
    color: var(--ink-body);
  }
  .brand { position: absolute; left: 32px; top: 92px; }
  .brand-name {
    font-family: "Montserrat", sans-serif;
    font-weight: 700;
    font-size: 28px;
    letter-spacing: -0.5px;
    color: var(--ink-dark);
    line-height: 1;
  }
  .brand-tagline {
    font-family: "Montserrat", sans-serif;
    font-weight: 500;
    font-size: 10.5px;
    color: var(--ink-dark);
    margin-top: 2px;
    letter-spacing: 0.2px;
  }
  .recipient { position: absolute; left: 41px; top: 292px; }
  .recipient-name {
    font-family: "Montserrat", sans-serif;
    font-weight: 700;
    font-size: 27px;
    color: var(--ink-grey);
    letter-spacing: 0.3px;
    margin-bottom: 8px;
  }
  .recipient-line { font-size: 15px; color: var(--ink-grey); line-height: 20px; margin-bottom: 8px; letter-spacing: 0.4px; }
  .recipient-address { line-height: 20px; }
  .letter-date {
    position: absolute;
    right: 44px;
    top: 400px;
    font-family: "Open Sans", sans-serif;
    font-weight: 600;
    font-size: 17px;
    color: var(--ink-grey);
  }
  .letter-body { position: absolute; left: 36px; width: 828px; }
  .letter-body p {
    font-size: 15.3px;
    line-height: 19.7px;
    text-align: justify;
    color: var(--ink-body);
  }
  .body-one { top: 454px; }
  .body-two { top: 592px; }
  .body-three { top: 730px; }
  .signoff-title {
    position: absolute;
    left: 576px;
    top: 870px;
    font-size: 22px;
    color: var(--ink-grey);
  }
  .signature-area {
    position: absolute;
    left: 596px;
    top: 920px;
    width: 168px;
    height: 100px;
    background: var(--signature-fill);
    border-radius: 4px;
  }
  .ghost-circle { position: absolute; left: 710px; top: 1040px; }
  .contact-bar {
    position: absolute;
    left: 0;
    top: 1143px;
    width: 624px;
    height: 29px;
    background: var(--brand-green);
    border-radius: 0 15px 15px 0;
    display: flex;
    align-items: center;
    padding-left: 36px;
    gap: 14px;
    color: var(--footer-text);
    font-size: 16.5px;
  }
  .contact-item { display: flex; align-items: center; gap: 4px; white-space: nowrap; }
  .contact-item svg { width: 14px; height: 14px; flex-shrink: 0; }
</style>
</head>
<body>
<main class="letterhead">
  <header class="brand">
    <div class="brand-name">VITARIDGE</div>
    <div class="brand-tagline">COMMUNITY HEALTH CENTER</div>
  </header>

  <section class="recipient">
    <h1 class="recipient-name">MARA ELLWOOD</h1>
    <p class="recipient-line">0198-274-365</p>
    <p class="recipient-line">info@northlanepartners.com</p>
    <p class="recipient-line recipient-address">5870 Harbor View Rd. Suite<br>210 Fairhaven, OR 0000</p>
  </section>

  <p class="letter-date">12 December, 2023</p>

  <section class="letter-body body-one">
    <p>Lorem ipsum dolor sit amet, consectetuer adipiscing elit, sed diam nonummy nibh euismod tincidunt ut laoreet dolore magna aliquam erat volutpat. Ut wisi enim ad minim veniam, quis nostrud exerci tation ullamcorper suscipit lobortis nisl ut aliquip ex ea commodo consequat. Duis autem vel eum iriure dolor in hendrerit in vulputate velit esse molestie consequat, vel illum dolore eu feugiat nulla facilisis at vero eros et accumsan et iusto odio dignissim qui blandit praesent luptatum zzril delenit augue duis dolore te feugait nulla facilisi.</p>
  </section>
  <section class="letter-body body-two">
    <p>Lorem ipsum dolor sit amet, cons ectetuer adipiscing elit, sed diam nonummy nibh euismod tincidunt ut laoreet dolore magna aliquam erat volutpat. Ut wisi enim ad minim veniam, quis nostrud exerci tation ullamcorper suscipit lobortis nisl ut aliquip ex ea commodo consequat.</p>
    <p>Lorem ipsum dolor sit amet, consectetuer adipiscing elit, sed diam nonummy nibh euismod tincidunt ut laoreet dolore magna aliquam erat</p>
  </section>
  <section class="letter-body body-three">
    <p>Lorem ipsum dolor sit amet, cons ectetuer adipiscing elit, sed diam nonummy nibh euismod tincidunt ut laoreet dolore magna aliquam erat volutpat. Ut wisi enim ad minim veniam, quis nostrud exerci tation ullamcorper suscipit lobortis nisl ut aliquip ex ea commodo consequat. Lorem ipsum dolor sit zamet, consectetuer adipiscing elit, sed diam nonummy nibh euismod tincidunt.</p>
  </section>

  <p class="signoff-title">Managing Director</p>
  <div class="signature-area" role="img" aria-label="Handwritten signature of the managing director"></div>

  <svg class="ghost-circle" width="54" height="54" viewBox="0 0 54 54" aria-hidden="true">
    <circle cx="27" cy="27" r="27" fill="var(--ghost)"/>
  </svg>

  <footer class="contact-bar">
    <span class="contact-item">
      <svg viewBox="0 0 16 16" aria-hidden="true"><circle cx="8" cy="8" r="8" fill="#fff"/><path d="M5.2 3.8l1.4 1.6-.7 1.1c.5 1.2 1.4 2.1 2.6 2.6l1.1-.7 1.6 1.4-.6 1.4c-3.3-.3-6-3-6.3-6.3z" fill="var(--brand-green)"/></svg>
      0198-274-365
    </span>
    <span class="contact-item">
      <svg viewBox="0 0 16 16" aria-hidden="true"><circle cx="8" cy="8" r="8" fill="#fff"/><rect x="4" y="5" width="8" height="6" rx="1" fill="none" stroke="var(--brand-green)" stroke-width="1.2"/><path d="M4.3 5.5L8 8.4l3.7-2.9" fill="none" stroke="var(--brand-green)" stroke-width="1.2"/></svg>
      info@vitaridge.org
    </span>
    <span class="contact-item">
      <svg viewBox="0 0 16 16" aria-hidden="true"><circle cx="8" cy="8" r="8" fill="#fff"/><g fill="none" stroke="var(--brand-green)" stroke-width="1"><circle cx="8" cy="8" r="4.5"/><ellipse cx="8" cy="8" rx="2" ry="4.5"/><path d="M3.5 8h9"/></g></svg>
      www.vitaridge.org
    </span>
  </footer>
</main>
</body>
</html>
```